Kelvaro.ch is looking for business card letterhead and envelope C5 with WOW effect

We need a strong business card for our company Kelvaro.ch, logo is available. You want a black or dark background on which the logo Stark r% 26 # 252; appears. Letterhead and envelope in C5 format should be in a similar design, but does not have to be We need a strong business card for our company Kelvaro.ch, logo is available. A black or dark background is desired, on which the logo Stark comes across. The letterhead and the envelope in C5 format should have a similar design.

Target Market(s)

Private customers as well as entrepreneurs

Contact Information for Business Card

E-mail: info@kelvaro-example.ch
Web.www.Kelvaro-example.ch
Tel: +41 ( 0 ) 79 482 6037
Adresse:
Lindenweg 14
9406 Tarnbach

Hier kann man Icons verwenden für Email,Tel und Adressse

Font styles to use
Other font styles liked:
• Dubai,bold

Colors

Designer to choose colors to be used in the design.

Requirements
Must have
• WOW effect
Nice to have
• R% 26 # 252; back business card with our service listings. - VEHICLE LABELING - SHOP WINDOW LABELING - STICKERS AND MUCH MORE ... in red color

```html
<!DOCTYPE html>
<html lang="en">
<head>
<meta charset="utf-8">
<title>Kelvaro.ch — Business Card</title>
<link rel="stylesheet" href="https://fonts.googleapis.com/css2?family=Saira:wght@600;800&family=Mulish:wght@400;600&display=swap">
<style>
  :root {
    --backdrop: #8a8c8f;
    --card-light: #ffffff;
    --card-dark: #1f1f1f;
    --accent: #ffc61a;
    --accent-soft: #ffe48a;
    --ink: #3a3a3a;
    --ink-muted: #6b6b6b;
  }
  * { margin: 0; padding: 0; box-sizing: border-box; }
  html, body { width: 1200px; height: 913px; overflow: hidden; }
  body {
    background: var(--backdrop);
    position: relative;
    font-family: "Mulish", Arial, sans-serif;
  }
  .card {
    position: absolute;
    width: 540px;
    height: 318px;
    border-radius: 18px;
    overflow: hidden;
    box-shadow: 0 10px 24px rgba(0,0,0,0.28);
  }
  .card--front { left: 70px; top: 90px; background: var(--card-light); }
  .card--back  { left: 590px; top: 500px; background: var(--card-dark); }

  .pattern-area {
    position: absolute;
    border-radius: 8px;
  }
  .card--front .pattern-area {
    left: 36px; top: 110px; width: 260px; height: 180px;
    background: linear-gradient(135deg, var(--accent) 0%, var(--accent-soft) 100%);
  }
  .card--back .pattern-area {
    left: 36px; top: 96px; width: 250px; height: 190px;
    background: linear-gradient(135deg, var(--accent) 0%, #d9a40c 100%);
  }

  .holder {
    position: absolute; right: 34px; top: 30px; text-align: right;
  }
  .holder__name {
    font-family: "Saira", Arial, sans-serif;
    font-weight: 800; font-size: 22px; letter-spacing: 0.5px;
    color: var(--accent); line-height: 1;
  }
  .holder__role {
    font-size: 13px; color: var(--ink-muted); letter-spacing: 1px; margin-top: 4px;
  }

  .address {
    position: absolute; right: 34px; top: 132px; text-align: right;
    font-size: 13px; color: var(--ink); line-height: 1.35;
  }
  .address__rule {
    display: block; margin: 8px 0 0 auto; width: 70px; height: 2px; background: var(--accent);
  }

  .contact {
    position: absolute; right: 34px; top: 210px; list-style: none;
    font-size: 13px; color: var(--ink); line-height: 1.65;
  }
  .contact__item { display: flex; align-items: center; justify-content: flex-end; gap: 8px; }
  .contact__icon { width: 13px; height: 13px; flex: none; }

  .brand {
    position: absolute; right: 30px; top: 44px;
    font-family: "Saira", Arial, sans-serif;
    font-weight: 800; font-size: 58px; letter-spacing: 1px;
    color: var(--accent); line-height: 1;
  }
  .services {
    position: absolute; right: 30px; top: 166px; list-style: none; text-align: right;
    font-family: "Saira", Arial, sans-serif;
    font-weight: 800; font-size: 15px; color: var(--accent); line-height: 1.55;
  }
  .services__item { display: flex; align-items: center; justify-content: flex-end; gap: 10px; }
  .services__item::after {
    content: ""; width: 9px; height: 9px; border-radius: 50%; background: var(--accent);
  }
</style>
</head>
<body>

  <section class="card card--front" aria-label="Business card front">
    <div class="pattern-area" role="img" aria-label="Yellow honeycomb pattern of filled and outlined hexagons"></div>

    <div class="holder">
      <p class="holder__name">ADRIEN VOLLMER</p>
      <p class="holder__role">DIRECTOR</p>
    </div>

    <div class="address">
      <p>Lindenweg 14</p>
      <p>9406 Tarnbach</p>
      <span class="address__rule"></span>
    </div>

    <ul class="contact">
      <li class="contact__item">+41 ( 0 ) 79 482 6037
        <svg class="contact__icon" viewBox="0 0 16 16" aria-hidden="true"><path fill="#ffc61a" d="M3.6 1.5l2.3 2.8-1.4 1.6c.9 2 2.5 3.6 4.6 4.6l1.6-1.4 2.8 2.3-1.5 2.3C6.6 13.4 2.6 9.4 1.3 3z"/></svg>
      </li>
      <li class="contact__item">info@kelvaro-example.ch
        <svg class="contact__icon" viewBox="0 0 16 16" aria-hidden="true"><rect x="1" y="3" width="14" height="10" rx="1" fill="#ffc61a"/><path d="M1.5 3.8L8 9l6.5-5.2" fill="none" stroke="#fff" stroke-width="1.3"/></svg>
      </li>
      <li class="contact__item">www.Kelvaro-example.ch
        <svg class="contact__icon" viewBox="0 0 16 16" aria-hidden="true"><circle cx="8" cy="8" r="7" fill="#ffc61a"/><path d="M1 8h14M8 1c-3 3.5-3 10.5 0 14M8 1c3 3.5 3 10.5 0 14" fill="none" stroke="#fff" stroke-width="1"/></svg>
      </li>
    </ul>
  </section>

  <section class="card card--back" aria-label="Business card back">
    <div class="pattern-area" role="img" aria-label="Yellow honeycomb pattern of filled and outlined hexagons"></div>
    <p class="brand">KELVARO.CH</p>
    <ul class="services">
      <li class="services__item">VEHICLE LABELING</li>
      <li class="services__item">SHOP WINDOW LABELING</li>
      <li class="services__item">STICKERS AND MUCH MORE</li>
    </ul>
  </section>

</body>
</html>
```